Junior Kickwell Hub needs modern,elegant Letterhead

Our school needs a modern Letterhead with header a footer for Electronic and Hardcopy. Busuness Cards, Envelopes and Powerpoint template.
The header/footer are to have:
The school name: Tobias Marelund Academy of Soccer
School moto - "I think, therefore I am"

Contact details: Address: 18 Lintel Avenue, Brookhollow, Harare, Zimbabwe

Mobiles: +263 77 418 3097, +263 77 530 6182
website (some of these things could be in the footer)
Email: pmarelund@tmaq.example
School website is www.tmaq.example

Registar of Deeds# KT417/2008

Industry/Entity Type

School

Font styles to use
Serif

```html
<!DOCTYPE html>
<html lang="en">
<head>
<meta charset="utf-8">
<title>Junior Kickwell Hub — Stationery</title>
<link href="https://fonts.googleapis.com/css2?family=Tinos:wght@400;700&family=Arimo:wght@400&display=swap" rel="stylesheet">
<style>
  :root {
    --backdrop: #6b6b6b;
    --paper: #ffffff;
    --ink: #333333;
    --ink-soft: #555555;
    --green: #1fae4b;
    --yellow: #f2b705;
    --maroon: #8b1a1a;
    --accent-red: #9b1c1c;
    --star-grey: #9a9a9a;
    --serif: "Tinos", "Times New Roman", serif;
    --sans: "Arimo", Arial, sans-serif;
  }
  * { box-sizing: border-box; margin: 0; padding: 0; }
  html, body { width: 1200px; height: 1000px; overflow: hidden; }
  body { background: var(--backdrop); font-family: var(--serif); color: var(--ink); position: relative; }

  .sheet { position: absolute; background: var(--paper); }

  /* brand lockup: name in one colour & weight with a plain circle */
  .brand { display: flex; align-items: center; gap: 8px; }
  .brand-dot { width: 22px; height: 22px; border-radius: 50%; background: var(--green); flex: none; }
  .brand-name { font-family: var(--serif); font-weight: 700; color: #222; line-height: 1.05; text-transform: uppercase; letter-spacing: .5px; }
  .motto { font-family: var(--serif); text-transform: uppercase; color: var(--ink); letter-spacing: .3px; }

  .contact { display: flex; align-items: center; gap: 5px; font-size: 11px; color: var(--ink-soft); white-space: nowrap; }
  .icon { width: 10px; height: 10px; flex: none; }

  /* letterhead */
  .letterhead { left: 28px; top: 58px; width: 675px; height: 872px; }
  .letterhead .brand { position: absolute; left: 44px; top: 30px; width: 200px; }
  .letterhead .brand-name { font-size: 13px; }
  .letterhead .motto { position: absolute; left: 60px; top: 95px; font-size: 12px; }
  .letterhead .phones { position: absolute; right: 38px; top: 33px; display: flex; gap: 18px; }
  .letterhead .corner-stars { position: absolute; right: 0; top: 0; }
  .letterhead .footer-text { position: absolute; left: 0; right: 0; bottom: 24px; text-align: center; font-size: 12px; color: var(--ink-soft); }
  .letterhead .footer-text small { display: block; font-size: 9px; margin-top: 3px; }
  .band { position: absolute; left: 0; right: 0; bottom: 0; height: 12px; display: flex; }
  .band i { display: block; height: 100%; }
  .band .g { background: var(--green); flex: 522; }
  .band .y { background: var(--yellow); flex: 78; }
  .band .m { background: var(--maroon); flex: 75; }

  /* envelope */
  .envelope { left: 370px; top: 150px; width: 780px; height: 320px; }
  .envelope .brand { position: absolute; left: 48px; top: 28px; width: 190px; }
  .envelope .brand-name { font-size: 12px; }
  .envelope .motto { position: absolute; left: 70px; top: 90px; font-size: 11px; }
  .envelope .address { position: absolute; left: 78px; bottom: 42px; font-size: 11px; color: var(--ink-soft); }
  .envelope .address small { display: block; font-size: 8px; margin-top: 2px; }
  .envelope .contacts { position: absolute; right: 40px; bottom: 26px; display: flex; gap: 14px; }
  .envelope .rule { position: absolute; left: 208px; right: 0; bottom: 48px; height: 4px; display: flex; }
  .envelope .rule .g { flex: 370; background: var(--green); }
  .envelope .rule .y { flex: 100; background: var(--yellow); }
  .envelope .rule .m { flex: 100; background: var(--maroon); }

  /* business cards */
  .card { left: 760px; width: 410px; height: 240px; }
  .card-back { top: 493px; }
  .card-back .faint-name { position: absolute; left: 30px; top: 70px; width: 340px; text-align: center; font-family: var(--serif); font-weight: 700; font-size: 30px; text-transform: uppercase; color: #e6e6e6; line-height: 1.1; }
  .card-back .person { position: absolute; left: 218px; top: 28px; }
  .card-back .person-name { font-family: var(--sans); font-size: 20px; color: var(--accent-red); }
  .card-back .person-role { font-size: 12px; color: var(--ink); }
  .card-back .details { position: absolute; left: 218px; top: 122px; display: flex; flex-direction: column; gap: 2px; }
  .card-back .details .contact { font-size: 12.5px; color: var(--ink); }
  .card-back .details .plain { padding-left: 0; line-height: 1.1; font-size: 12.5px; }

  .card-front { top: 750px; }
  .card-front .brand { position: absolute; left: 0; right: 0; top: 60px; justify-content: center; }
  .card-front .brand-dot { width: 34px; height: 34px; }
  .card-front .brand-name { font-size: 19px; width: 250px; }
  .card-front .motto { position: absolute; left: 0; right: 0; top: 183px; text-align: center; font-size: 15px; }
</style>
</head>
<body>

<svg width="0" height="0" style="position:absolute" aria-hidden="true">
  <defs>
    <symbol id="icon-phone" viewBox="0 0 10 10">
      <rect width="10" height="10" rx="2" fill="#c0282d"/>
      <rect x="3" y="1.8" width="4" height="6.4" rx=".8" fill="#fff"/>
      <rect x="3.8" y="2.6" width="2.4" height="4" fill="#c0282d"/>
    </symbol>
    <symbol id="icon-mail" viewBox="0 0 10 10">
      <rect width="10" height="10" rx="2" fill="#c0282d"/>
      <rect x="2" y="3" width="6" height="4.2" fill="#fff"/>
      <path d="M2 3 L5 5.5 L8 3" stroke="#c0282d" stroke-width=".8" fill="none"/>
    </symbol>
    <symbol id="icon-web" viewBox="0 0 10 10">
      <rect width="10" height="10" rx="2" fill="#c0282d"/>
      <circle cx="5" cy="5" r="2.8" fill="none" stroke="#fff" stroke-width="1"/>
      <path d="M2.2 5 H7.8 M5 2.2 V7.8" stroke="#fff" stroke-width=".7"/>
    </symbol>
  </defs>
</svg>

<!-- Letterhead -->
<section class="sheet letterhead">
  <div class="brand"><span class="brand-dot"></span><span class="brand-name">Tobias Marelund Academy of Soccer</span></div>
  <p class="motto">I think, therefore I am</p>
  <div class="phones">
    <span class="contact"><svg class="icon"><use href="#icon-phone"/></svg>+263 77 418 3097</span>
    <span class="contact"><svg class="icon"><use href="#icon-phone"/></svg>+263 77 530 6182</span>
  </div>
  <svg class="corner-stars" width="34" height="30" viewBox="0 0 34 30" aria-hidden="true">
    <polygon fill="var(--star-grey)" points="25,2 27.3,8 33.5,8 28.5,11.8 30.4,18 25,14.2 19.6,18 21.5,11.8 16.5,8 22.7,8"/>
    <polygon fill="var(--star-grey)" points="9,14 10.8,18.6 15.6,18.6 11.7,21.5 13.2,26.2 9,23.3 4.8,26.2 6.3,21.5 2.4,18.6 7.2,18.6"/>
  </svg>
  <p class="footer-text">18 Lintel Avenue, Brookhollow Harare, Zimbabwe, pmarelund@tmaq.example, &nbsp;www.tmaq.example
    <small>Registar of Deeds# KT417/2008</small></p>
  <div class="band"><i class="g"></i><i class="y"></i><i class="m"></i></div>
</section>

<!-- Envelope -->
<section class="sheet envelope">
  <div class="brand"><span class="brand-dot"></span><span class="brand-name">Tobias Marelund Academy of Soccer</span></div>
  <p class="motto">I think, therefore I am</p>
  <p class="address">18 Lintel Avenue, Brookhollow Harare, Zimbabwe<small>Registar of Deeds# KT417/2008</small></p>
  <div class="rule"><i class="g"></i><i class="y"></i><i class="m"></i></div>
  <div class="contacts">
    <span class="contact"><svg class="icon"><use href="#icon-phone"/></svg>+263 77 418 3097</span>
    <span class="contact"><svg class="icon"><use href="#icon-phone"/></svg>+263 77 530 6182</span>
    <span class="contact"><svg class="icon"><use href="#icon-mail"/></svg>pmarelund@tmaq.example</span>
    <span class="contact"><svg class="icon"><use href="#icon-web"/></svg>www.tmaq.example</span>
  </div>
</section>

<!-- Business card: details side -->
<section class="sheet card card-back">
  <p class="faint-name">Tobias Marelund Academy of Soccer</p>
  <div class="person">
    <p class="person-name">Daniel Ostrowe</p>
    <p class="person-role">Director</p>
  </div>
  <div class="details">
    <span class="contact"><svg class="icon"><use href="#icon-phone"/></svg>+263 77 418 3097</span>
    <span class="contact"><svg class="icon"><use href="#icon-phone"/></svg>+263 77 530 6182</span>
    <span class="contact"><svg class="icon"><use href="#icon-mail"/></svg>pmarelund@tmaq.example</span>
    <span class="contact"><svg class="icon"><use href="#icon-web"/></svg>www.tmaq.example</span>
    <span class="plain">18 Lintel Avenue, Brookhollow<br>Harare, Zimbabwe</span>
  </div>
</section>

<!-- Business card: brand side -->
<section class="sheet card card-front">
  <div class="brand"><span class="brand-dot"></span><span class="brand-name">Tobias Marelund Academy of Soccer</span></div>
  <p class="motto">I think, therefore I am</p>
</section>

</body>
</html>
```